Car rental website design for a UAE car rental company

This project is about creating a new website design for a car rental company located in Dubai (United Arab Emirates), I opened the same project a few months ago but I didn't receive a lot of appealing entries so I closed it but this time I am marking the project as guaranteed to avoid such situation again, if you have already provided a design before then please re-submit again on this project so that it is considered while reviewing all the designs

A few important things:

1- We need a simple non-complex design
2- The final deliverable would be 2 screens (PSD, JPEG ... etc), the first screen is for the home page and the second screen is for an internal page
3- The home page must have a section that end users can use to rent a car online directly from the home page instead of going into some inner pages
4- The current website is very old and not very appealing so avoid creating a similar design (www.crestvane-autos.example)
5- The name is Crestvane but the company rents normal cars (no Limousin cars will be rented) so avoid adding any fancy cars in the images/graphics used in the design, just normal end users cars
6- The expected pages would be: home, About us, Our team, Strategy, Contact us and links to social media pages
7- The attachments include the company's logo and some screens from other car rental companies that provide online rentals/payments

If you have any questions please feel free to ask and please note that we will need the designs urgently

Thanks

Target Market(s)

Dubai - United Arab Emirates

Industry/Entity Type

It Company

Number of Pages Required

2 page

Font styles to use
Sans Serif

Requirements
Must have
• Check the project details
Nice to have
Should not have

```html
<!DOCTYPE html>
<html lang="en">
<head>
<meta charset="utf-8">
<title>Crestvane – Car Rental Dubai</title>
<link href="https://fonts.googleapis.com/css2?family=Open+Sans:wght@400;600;700;800&display=swap" rel="stylesheet">
<style>
:root{
  --white:#ffffff;
  --orange:#f15a24;
  --ink:#333333;
  --soft-bg:#fafafa;
  --card-grey:#b9b9b9;
  --booking-bg:#2b2726;
  --footer-bg:#0c3a52;
  --brand-red:#c8262f;
  --offer-1:#1e3d4f;
  --offer-2:#e3e1cf;
  --offer-3:#69bccb;
  --offer-4:#4a5168;
}
*{box-sizing:border-box;margin:0;padding:0}
html,body{width:812px;height:1200px;overflow:hidden}
body{position:relative;font-family:"Open Sans",Arial,sans-serif;background:var(--white);color:var(--ink)}
.abs{position:absolute}

/* header */
.site-header{left:0;top:0;width:812px;height:24px;background:var(--white);z-index:5}
.brand{display:flex;align-items:center;gap:3px}
.brand-mark{width:7px;height:7px;background:var(--brand-red)}
.brand-name{font-weight:700;color:var(--ink)}
.site-header .brand{left:238px;top:6px}
.site-header .brand-name{font-size:10px}
.main-nav a{position:absolute;top:6px;font-size:7px;color:var(--ink);text-decoration:none;white-space:nowrap}

/* hero */
.hero{left:0;top:0;width:812px;height:394px;
  background:linear-gradient(180deg,#b7c3cc 0%,#9aa3a6 35%,#c7b69d 60%,#6c7a86 100%)}
.hero-photo{left:202px;top:19px;width:410px;height:209px;
  background:linear-gradient(160deg,#5a5048 0%,#2e2a27 45%,#121212 70%,#6f6a63 100%)}
.hero-title{left:202px;top:101px;width:410px;text-align:center;color:var(--white);
  font-weight:800;font-size:15px;letter-spacing:.6px}
.btn{display:block;background:var(--orange);color:var(--white);text-align:center;text-decoration:none}
.hero-btn{left:362px;top:227px;width:89px;height:24px;line-height:24px;font-size:7px}
.hero-text{left:234px;top:288px;width:348px;color:var(--white);font-size:7px;line-height:9px;text-indent:10px}

/* offers */
.offers{left:0;top:394px;width:812px;height:200px;background:var(--soft-bg)}
.section-title{width:812px;left:0;text-align:center;font-size:10px;letter-spacing:.5px}
.offers .section-title{top:14px;color:var(--ink)}
.offer{width:90px;text-align:center}
.offer-icon{width:58px;height:58px;border-radius:50%;margin:0 auto}
.offer-label{margin-top:4px;font-size:6.5px;line-height:8px;color:var(--ink)}

/* testimonials */
.testimonial .avatar{position:absolute;left:0;top:0;width:46px;height:46px;border-radius:50%;
  background:linear-gradient(180deg,#e9e4df,#b9c3cc);border:2px solid var(--white);box-shadow:0 0 0 1px #ddd}
.testimonial .quote{position:absolute;left:38px;top:10px;width:126px;height:34px;background:var(--card-grey);
  color:var(--white);font-size:5px;line-height:6.5px;padding:4px 5px 4px 12px;text-align:right}
.testimonial .quote.short{height:32px;top:10px;padding-top:10px}

/* booking */
.booking{left:0;top:811px;width:812px;height:293px;background:var(--booking-bg)}
.booking .section-title{top:14px;color:var(--white)}
.booking-form{left:371px;top:52px;width:91px}
.field label{display:block;text-align:center;color:var(--white);font-size:6px;line-height:8px}
.field .input{height:11px;background:var(--white);color:#bbb;font-size:5.5px;line-height:11px;padding-left:10px;margin-bottom:5px}
.field .textarea{height:34px;line-height:9px}
.booking-btn{left:389px;top:252px;width:55px;height:12px;line-height:12px;font-size:6px}

/* footer */
.site-footer{left:0;top:1104px;width:812px;height:96px;background:var(--footer-bg)}
.footer-brand{left:244px;top:6px;width:46px;height:40px;background:var(--white);border-radius:4px;
  justify-content:center;flex-direction:column;gap:2px}
.footer-brand .brand-name{font-size:7.5px}
.footer-nav a{position:absolute;top:20px;font-size:6px;color:var(--white);text-decoration:none;white-space:nowrap}
.copyright{left:328px;top:43px;font-size:5.5px;color:#d6e1e7}
</style>
</head>
<body>

<section class="hero abs" role="img" aria-label="Blurred Dubai city skyline background"></section>
<div class="hero-photo abs" role="img" aria-label="Dark sedan parked beside an industrial building"></div>
<h1 class="hero-title abs">Welcome to Crestvane</h1>
<a class="btn hero-btn abs" href="#book">Book this Car now</a>
<p class="hero-text abs">As Dubai is expected to welcome millions of tourists and visitors, car rental industry is believed to escalate more rapidly in the region. Over the past five years, demands for car rentals in Dubai has been augmenting at a healthy pace and is currently registering a growth rate of 20 to 25 percent per year. The swift economic growth and the number of projects in Dubai have been attracting businessmen, tourism and construction companies to the UAE. All of these have greatly contributed to the growth of the car rental industry including the government's decision to privatise transport services.</p>

<header class="site-header abs">
  <div class="brand abs"><span class="brand-mark"></span><span class="brand-name">Crestvane</span></div>
  <nav class="main-nav">
    <a href="#" style="left:324px">Home</a>
    <a href="#book" style="left:381px">Book Now</a>
    <a href="#" style="left:444px">About Us</a>
    <a href="#" style="left:506px">Our Team</a>
    <a href="#" style="left:569px">Strategy</a>
  </nav>
</header>

<section class="offers abs">
  <h2 class="section-title abs">We Offer</h2>
  <div class="offer abs" style="left:226px;top:59px">
    <div class="offer-icon" style="background:var(--offer-1)" role="img" aria-label="Thumbs up icon"></div>
    <p class="offer-label">Guaranteed<br>Satisfaction</p>
  </div>
  <div class="offer abs" style="left:320px;top:59px">
    <div class="offer-icon" style="background:var(--offer-2)" role="img" aria-label="Red car icon"></div>
    <p class="offer-label">Comfortable<br>Cars</p>
  </div>
  <div class="offer abs" style="left:413px;top:59px">
    <div class="offer-icon" style="background:var(--offer-3)" role="img" aria-label="Tools icon"></div>
    <p class="offer-label">24x7 Car<br>Maintenance</p>
  </div>
  <div class="offer abs" style="left:507px;top:59px">
    <div class="offer-icon" style="background:var(--offer-4)" role="img" aria-label="Banknote icon"></div>
    <p class="offer-label">Value for Money</p>
  </div>
</section>

<section class="testimonials">
  <div class="testimonial abs" style="left:244px;top:653px">
    <p class="quote">“Booking was quick and easy, the car was clean and ready on time. I will surely rent again soon.” - Sara M.</p>
    <div class="avatar" role="img" aria-label="Customer portrait"></div>
  </div>
  <div class="testimonial abs" style="left:428px;top:653px">
    <p class="quote">“Booking was quick and easy, the car was clean and ready on time. I will surely rent again soon.” - Sara M.</p>
    <div class="avatar" role="img" aria-label="Customer portrait"></div>
  </div>
  <div class="testimonial abs" style="left:244px;top:717px">
    <p class="quote short">“Why not rent your next car with us?” - Omar K.</p>
    <div class="avatar" role="img" aria-label="Customer portrait"></div>
  </div>
  <div class="testimonial abs" style="left:428px;top:717px">
    <p class="quote short">“Why not rent your next car with us?” - Omar K.</p>
    <div class="avatar" role="img" aria-label="Customer portrait"></div>
  </div>
</section>

<section class="booking abs" id="book">
  <h2 class="section-title abs">Book Now for a Ride</h2>
  <form class="booking-form abs">
    <div class="field"><label>Name:</label><div class="input">Enter Name</div></div>
    <div class="field"><label>Email:</label><div class="input">Enter Email</div></div>
    <div class="field"><label>Company:</label><div class="input">Enter Company</div></div>
    <div class="field"><label>Work Address:</label><div class="input">Enter Address</div></div>
    <div class="field"><label>City:</label><div class="input">Enter City</div></div>
    <div class="field"><label>Country:</label><div class="input">Enter Country</div></div>
    <div class="field"><label>Message:</label><div class="input textarea">Enter Your Message</div></div>
  </form>
  <a class="btn booking-btn abs" href="#">Book Now</a>
</section>

<footer class="site-footer abs">
  <div class="brand footer-brand abs"><span class="brand-mark"></span><span class="brand-name">Crestvane</span></div>
  <nav class="footer-nav">
    <a href="#" style="left:338px">Home</a>
    <a href="#" style="left:378px">About us</a>
    <a href="#" style="left:421px">Book Now</a>
    <a href="#" style="left:466px">Our Team</a>
    <a href="#" style="left:511px">Strategy</a>
  </nav>
  <p class="copyright abs">Copyright 2015, Crestvane. All rights reserved.</p>
</footer>

</body>
</html>
```